Book cover

I need a cover for a my 3rd book that kinda goes with my brand (my previous book. The name of my first book - "Turbulence Behind the Yoke" Hidden Strain Inside Modern Cockpits: A Guide for Travelers". In the same style I need my third book - NO HARBOR" to stand out. I need a bolder, less whimsy cover, less playful. So can we use some of the same elements to stay consistent in this book cover. Perhaps use text to envoke emotions. This is the back cover so far (see below attachemnent)

Hello,
Subject: Cover Direction & Brand Consistency

Hi everyone,

Here’s my honest take: I don’t think the current execution fully reflects my brand yet. What I’m wondering is whether we can bring more continuity across my books—borrowing elements from my first and second covers to inform this third one. Think of how authors like Dorian Welk maintain a recognizable style across their work. That consistency builds trust and signals authority before a reader even opens the book. Design choices like this matter more than we realize.

I’ve attached a cover I came across on Brindlemart that reminded me of Option 5 and feels aligned with where you’re headed. One thought: could we experiment with introducing a crack—or cracks—into the word HARBOR itself? Maybe put the title "NO HARBOR" at the edge of the cover vertically?

Curious to hear your thoughts and how you see this evolving.
P.s. Is there away to attach an idea?

NO HARBOR: Restoring Quiet Edges in a Culture that Praises Hurry

```html
<!DOCTYPE html>
<html lang="en">
<head>
<meta charset="utf-8">
<title>NO HARBOR – Book Cover</title>
<link rel="stylesheet" href="https://fonts.googleapis.com/css2?family=Montserrat:wght@400;500;600;700&family=Roboto:wght@400&family=Roboto+Condensed:wght@600;700&family=Archivo+Black&family=Oswald:wght@500&display=swap">
<style>
  :root{
    --navy:#1a2330;
    --navy-deep:#0c1219;
    --cyan:#1fb3e8;
    --white:#ffffff;
    --text:#e6e9ee;
    --gold:#d9a63a;
    --sky-light:#c7dcec;
    --sky-mid:#3f7fae;
    --sky-deep:#0f3c63;
  }
  html,body{margin:0;padding:0;width:1200px;height:882px;overflow:hidden;background:var(--navy-deep);}
  .cover{position:relative;width:1200px;height:882px;overflow:hidden;font-family:"Montserrat",sans-serif;}
  .back{position:absolute;left:0;top:0;width:580px;height:882px;
    background:linear-gradient(180deg,var(--navy) 0%,#18212d 60%,var(--navy-deep) 100%);}
  .sky{position:absolute;left:570px;top:0;width:630px;height:882px;
    background:
      radial-gradient(ellipse 55% 30% at 62% 30%,rgba(220,232,242,.85),rgba(220,232,242,0) 70%),
      radial-gradient(ellipse 40% 25% at 40% 80%,rgba(190,210,228,.55),rgba(190,210,228,0) 70%),
      linear-gradient(180deg,var(--sky-deep) 0%,var(--sky-mid) 35%,#4c86b2 60%,var(--sky-deep) 100%);}
  .sky::before{content:"";position:absolute;inset:0;
    background:linear-gradient(90deg,rgba(12,18,25,.9) 0%,rgba(12,18,25,0) 14%);}
  .headline{position:absolute;left:37px;top:38px;width:500px;margin:0;
    color:var(--cyan);font-weight:600;font-size:18.6px;line-height:18px;letter-spacing:.1px;}
  .blurb{position:absolute;left:37px;top:122px;width:484px;margin:0;
    color:var(--text);font-size:12.3px;line-height:17.7px;text-align:justify;}
  .blurb p{margin:0;}
  .bio{position:absolute;left:37px;top:550px;width:377px;margin:0;
    color:var(--text);font-size:10.4px;line-height:12.7px;}
  .bio p{margin:0;}
  .bio .justified{text-align:justify;}
  .bio strong{font-weight:600;letter-spacing:.3px;}
  .author-photo{position:absolute;left:423px;top:557px;width:96px;height:130px;
    background:linear-gradient(160deg,#5a5f66 0%,#2b2f36 55%,#1b2330 100%);}
  .imprint{position:absolute;left:48px;top:800px;display:flex;align-items:center;gap:6px;
    color:var(--gold);font-weight:600;font-size:11px;letter-spacing:1.5px;line-height:12px;}
  .imprint .dot{width:12px;height:12px;border-radius:50%;background:var(--gold);}
  .price{position:absolute;left:212px;top:814px;color:var(--white);
    font-family:"Oswald",sans-serif;font-weight:500;font-size:10.5px;line-height:14px;}
  .spine-text{position:absolute;left:612px;top:58px;transform-origin:0 0;transform:rotate(90deg);
    color:var(--white);font-family:"Roboto",sans-serif;font-size:14.5px;white-space:nowrap;}
  .spine-author{top:624px;}
  .title-stack{position:absolute;left:1082px;top:70px;width:70px;margin:0;
    color:var(--white);font-family:"Archivo Black",sans-serif;font-size:72px;line-height:81px;text-align:center;}
  .title-stack span{display:block;}
  .subtitle{position:absolute;left:643px;top:522px;margin:0;
    color:var(--white);font-family:"Roboto Condensed",sans-serif;font-weight:700;font-size:52px;line-height:55px;letter-spacing:-.5px;}
  .author{position:absolute;left:643px;top:760px;margin:0;
    color:var(--cyan);font-family:"Roboto Condensed",sans-serif;font-weight:700;font-size:31px;line-height:34px;}
</style>
</head>
<body>
<div class="cover">
  <section class="back">
    <h2 class="headline">Women have been told we could do and be anything … and we can.<br>What’s rarely mentioned is the toll on our health, relationships, and overall wellbeing.</h2>
    <div class="blurb">
      <p>Are you the woman who holds it all together—crushing deadlines, leading teams, raising a family—while quietly unraveling inside? Yes, you are competent and capable. You’ve simply been carrying more than you were ever meant to for too long.</p>
      <p>No Harbor offers a different way forward. Drawn from decades of experience flying commercial aircraft and championing women's health, retired Captain Linnea Varga reveals the missing skill most high-achieving women were never taught: protecting your margins in a world that glorifies overload. This vital buffer not only enables recovery after near-collapse, but also prevents you from reaching the breaking point of exhaustion.</p>
      <p>You will learn about the centuries-old mindset when humans first became cogs in the machine, the science of burnout and brain rewiring, the psychology driving us to push limits, and the cultural systems rigged against women. Discover how to spot the three stages of depletion before they ground you. Through self-assessment tools and actionable practices, the author guides us back home to ourselves by offering a roadmap to rebuild our strength, reconnect with joy and purpose, and redefine success to include true wellbeing.</p>
      <p>You don’t need to crash to earn a soft landing. Buckle up! No Harbor is your wakeup call to fly lighter and higher than you ever imagined.</p>
      <p>Linnea Varga is a speaker, consultant, and founder of the Flightline Wellness Institute. With over 10,000 flight hours, she now empowers women to successfully lead without losing themselves.</p>
    </div>
    <div class="bio">
      <p class="justified"><strong>CAPTAIN LINNEA VARGA</strong> is the founder of Cleared to Thrive, an aviation-based wellbeing organization that builds on her 34+ years of experience as a commercial airline pilot. She helps others in high-performance professions and those seeking careers as airline pilots achieve a healthier, more rewarding life using practical techniques tailored for their careers. She currently captains wide-body aircrafts and has logged over 10,000 hours of jet flight time.</p>
      <p>Linnea has over a decade of experience in health and wellbeing as an aviation strategist. She is certified in Mindfulness Based Stress Reduction (MBSR) at Eastbrook University and earned a BS in Leadership (Sigma Tau Rho) and an Executive Certificate in Business from Westhaven University.</p>
      <p>Having travelled the globe repeatedly, Linnea's favorite place in the world is with her family, spending time on the east and west coast of the US. She enjoys gardening, meditation, and the love of learning.</p>
    </div>
    <div class="author-photo" role="img" aria-label="Portrait of the author in a pilot's uniform standing beside a jet engine"></div>
    <div class="imprint"><span class="dot"></span><span>EMBERLINE<br>PRESS</span></div>
    <div class="price">US $19.99<br>CA $23.99</div>
  </section>

  <div class="sky" role="img" aria-label="Passenger jet flying head-on toward the viewer through a blue sky with motion-streaked clouds"></div>

  <div class="spine-text">NO HARBOR: Restoring Quiet Edges in a Culture that Praises Hurry</div>
  <div class="spine-text spine-author">Capt. Linnea Varga</div>

  <h1 class="title-stack"><span>N</span><span>O</span><span>&nbsp;</span><span>H</span><span>A</span><span>R</span><span>B</span><span>O</span><span>R</span></h1>
  <p class="subtitle">Restoring Quiet<br>Edges in a<br>Culture that<br>Praises Hurry</p>
  <p class="author">Capt. Linnea Varga</p>
</div>
</body>
</html>
```